Corvel Capital LLC

Need Professional Business cards for New Investment Fund

Target Market(s)

High Quality investors

Industry/Entity Type

Financial

Contact Information for Business Card

Phone Number +1 555 284 6190
Name Lukas Varenko
Title Fund Manager
email lv@FundCorvel.com
Website www.FundCorvel.com

Colors

Designer to choose colors to be used in the design.

Requirements
Must have
• Must have our Logo and all of the above. Must be made so lettering and loge can be raised

```html
<!DOCTYPE html>
<html lang="en">
<head>
<meta charset="utf-8">
<title>Business Card – Lukas Varenko, Fund Manager</title>
<link href="https://fonts.googleapis.com/css2?family=Open+Sans:wght@400;600;700&display=swap" rel="stylesheet">
<style>
  :root {
    --page: #3a322e;
    --card: #1c1e1f;
    --green: #2ee62a;
    --slate: #4a5348;
    --muted: #7d827d;
    --white: #e8ebe8;
  }
  * { margin: 0; padding: 0; box-sizing: border-box; }
  html, body { width: 1200px; height: 864px; overflow: hidden; }
  body {
    background: var(--page);
    font-family: "Open Sans", Arial, sans-serif;
    position: relative;
  }
  .card {
    position: absolute;
    width: 560px;
    height: 320px;
    background: var(--card);
    box-shadow: 0 10px 28px rgba(0,0,0,.45);
    overflow: hidden;
  }
  .card-front { left: 70px; top: 90px; }
  .card-back { left: 570px; top: 450px; }

  /* front */
  .front-brand {
    position: absolute;
    inset: 0;
    display: flex; align-items: center; justify-content: center; gap: 14px;
  }
  .brand-square { width: 22px; height: 22px; background: var(--green); }
  .brand-name {
    font-weight: 600;
    font-size: 40px;
    letter-spacing: 4px;
    color: var(--green);
    text-transform: uppercase;
    white-space: nowrap;
  }

  /* back */
  .accent-bar { position: absolute; left: 44px; top: 66px; width: 8px; }
  .accent-bar .top { height: 34px; background: var(--green); }
  .accent-bar .bottom { height: 34px; background: var(--slate); }
  .holder { position: absolute; left: 70px; top: 62px; }
  .holder-name {
    font-weight: 700; font-size: 19px; color: var(--green);
    text-transform: uppercase; letter-spacing: .5px;
  }
  .holder-title { font-weight: 600; font-size: 15px; color: var(--white); margin-top: 1px; }
  .rule {
    position: absolute; left: 70px; top: 122px; width: 400px;
    height: 2px; background: var(--green);
  }
  .contacts { position: absolute; left: 70px; top: 136px; list-style: none; }
  .contacts li {
    display: flex; align-items: center; gap: 9px;
    font-size: 13px; color: var(--muted); height: 21px;
  }
  .contacts svg { width: 12px; height: 12px; fill: var(--green); flex: none; }
  .back-brand {
    position: absolute; right: 36px; bottom: 40px;
    display: flex; align-items: center; gap: 10px;
  }
  .back-brand .brand-square { width: 16px; height: 16px; }
  .back-brand .brand-name { font-size: 28px; letter-spacing: 3px; }
</style>
</head>
<body>
  <section class="card card-front" aria-label="Card front">
    <div class="front-brand">
      <span class="brand-square"></span>
      <span class="brand-name">Veltrane</span>
    </div>
  </section>

  <section class="card card-back" aria-label="Card back">
    <div class="accent-bar"><div class="top"></div><div class="bottom"></div></div>
    <div class="holder">
      <p class="holder-name">Lukas Varenko</p>
      <p class="holder-title">Fund Manager</p>
    </div>
    <div class="rule"></div>
    <ul class="contacts">
      <li>
        <svg viewBox="0 0 12 12"><path d="M1 3c0-1 1-2 2-2h6c1 0 2 1 2 2v1H8V3H4v1H1z M2 5h8l1 6H1z"/></svg>
        +1 555 284 6190
      </li>
      <li>
        <svg viewBox="0 0 12 12"><path d="M0 2h12v1L6 7 0 3z M0 4.5l6 4 6-4V10H0z"/></svg>
        lv@FundCorvel.com
      </li>
      <li>
        <svg viewBox="0 0 12 12"><circle cx="6" cy="6" r="5.5"/><path d="M6 1v10M1 6h10" stroke="#1c1e1f" stroke-width="1"/></svg>
        www.FundCorvel.com
      </li>
    </ul>
    <div class="back-brand">
      <span class="brand-square"></span>
      <span class="brand-name">Veltrane</span>
    </div>
  </section>
</body>
</html>
```